International Medical Company Needs a Website Design for a Support Site

We need a website design for a support site we are doing for ostomates called Bright Returns. We are an international company but this website is for our Australian market.

The website is a support site for people who are living with an Ostomy or Bowel Disease. This is a site where they can read other ostomates' stories and how they are dealing with the fact that they have to wear a pouch everyday.

The URL for our US site is: http://www.brightreturnsite.example/

We need to use the same logo but we have freedom around the color scheme. We are not fond of the brown color scheme used in our US site and are happy for designs to be submitted with alternatives.

• We want the design to be clean, inspiring, modern and inviting.
• We would like to see a design for the mainpage / homepage and one of the subpages
• We only require the PSD / image files (no HTML needed)

Attached to this project is our sitemap, an example wireframe and the logos. We are happy for you to play around with different options and don't have to stick to the layout shown in the wireframe.

If you have any further questions please ask.

Industry/Entity Type

It Company

```html
<!DOCTYPE html>
<html lang="en">
<head>
<meta charset="utf-8">
<title>Bright Returns – Sharing Stories and Giving Hope</title>
<link href="https://fonts.googleapis.com/css2?family=Open+Sans:ital,wght@0,400;0,600;1,400&display=swap" rel="stylesheet">
<style>
:root{
  --brown:#7a5426;
  --brown-dark:#6a4719;
  --brown-light:#93682f;
  --frame:#b8a07c;
  --text:#555;
  --muted:#777;
  --nav-text:#444;
  --footer:#3b3b3b;
  --white:#fff;
  --fb:#3b5998;
  --tw:#29a3dc;
  --rss:#f26c1b;
  --yt:#d9262b;
}
*{box-sizing:border-box;margin:0;padding:0}
html,body{width:1200px;height:1178px;overflow:hidden;background:var(--white)}
body{font-family:"Open Sans",Arial,sans-serif;color:var(--text);position:relative}
.abs{position:absolute}
.line{display:block;white-space:nowrap}

/* header */
.site-header{position:absolute;left:0;top:0;width:1200px;height:180px;border-top:8px solid #f0f0f0}
.lang-switch{left:1008px;top:6px;width:104px;height:31px;border:1px solid #ddd;border-top:none;border-radius:0 0 4px 4px;background:linear-gradient(#fafafa,#ececec);display:flex;align-items:center;gap:8px;padding-left:20px;font-size:14px;color:#666}
.lang-switch .caret{margin-left:12px;width:0;height:0;border-left:5px solid transparent;border-right:5px solid transparent;border-top:6px solid #555}
.brand-name{left:86px;top:136px;font-size:18px;font-weight:600;letter-spacing:1px;color:var(--brown)}
.btn-dark{left:953px;top:82px;width:158px;height:43px;background:linear-gradient(#4a4a4a,#2c2c2c);border-radius:4px;color:#fff;font-size:18px;display:flex;align-items:center;justify-content:center}

/* nav */
.main-nav{left:0;top:180px;width:1200px;height:46px;background:linear-gradient(#fdfdfd,#ededed);border-top:1px solid #ddd}
.main-nav ul{list-style:none;position:absolute;left:86px;top:0;height:45px;display:flex}
.main-nav li{height:45px;display:flex;align-items:center;padding:0 26px;font-size:17px;color:var(--nav-text);position:relative}
.main-nav li+li::before{content:"";position:absolute;left:0;top:8px;height:29px;border-left:1px dotted #bbb}
.main-nav li:first-child{padding:0 23px}
.main-nav li.active{background:var(--brown);color:#fff}
.main-nav li.active+li::before{display:none}

/* hero */
.hero{left:0;top:226px;width:1200px;height:378px;background:linear-gradient(var(--brown-light),var(--brown-dark))}
.hero h1{position:absolute;left:84px;top:90px;font-weight:400;font-size:32.5px;color:#fff;white-space:nowrap}
.hero p{position:absolute;left:86px;top:156px;font-size:16.8px;line-height:29px;color:#fff}
.btn-outline{position:absolute;top:234px;height:44px;border:1.5px solid #fff;color:#fff;font-size:18px;display:flex;align-items:center;justify-content:center}
.hero .or{position:absolute;left:276px;top:242px;font-size:18px;color:#fff}
.dots{position:absolute;left:88px;top:324px;display:flex;gap:11px}
.dots span{width:16px;height:16px;border-radius:50%;background:#c8b49a;box-shadow:inset 0 1px 2px rgba(0,0,0,.3)}
.dots span:first-child{background:#f4f4f4}
.hero-photo{position:absolute;left:634px;top:49px;width:428px;height:290px;border:7px solid var(--frame);background:linear-gradient(#3f7fc4 0%,#a8c6e3 45%,#6d6a66 70%,#3b3733 100%)}

/* content */
.col-title{position:absolute;top:656px;font-size:24.5px;font-weight:400;color:var(--brown);white-space:nowrap}
.about-photo{left:88px;top:722px;width:288px;height:152px;background:linear-gradient(#4f8fd3,#b7d4ef 75%,#d9d3cc)}
.about-text{left:86px;top:895px;font-size:15.5px;line-height:29px;color:var(--muted)}
.quote{left:470px;top:727px;font-size:13.8px;line-height:24px;font-style:italic;color:#555;letter-spacing:-.1px}
.qmark{font-size:30px;color:#ccc;font-family:Georgia,serif}
.avatar{left:468px;top:900px;width:68px;height:64px;background:linear-gradient(#efe7e2,#b9a59a)}
.author-role{left:568px;top:914px;font-size:13.5px;font-weight:600;color:#333;white-space:nowrap}
.author-name{left:568px;top:944px;font-size:13.5px;font-weight:600;color:#333;display:flex;align-items:center;gap:10px;white-space:nowrap}
.news-item{position:absolute;left:806px;width:320px}
.news-item h3{font-size:15.5px;font-weight:400;color:var(--brown);margin-left:2px;white-space:nowrap}
.news-item time{display:block;margin-top:12px;font-size:13.8px;color:#666}
.news-item p{margin-top:6px;margin-left:2px;font-size:15.5px;line-height:25px;color:#555}
.news-rule{left:806px;top:849px;width:316px;border-top:1px dotted #999}

/* footer */
.site-footer{left:0;top:1043px;width:1200px;height:135px;background:var(--footer);color:#fff;font-family:Arial,"Open Sans",sans-serif}
.footer-links{position:absolute;left:92px;top:48px;font-size:14.5px}
.copyright{position:absolute;left:92px;top:81px;font-size:14.5px}
.social{position:absolute;top:54px;width:36px;height:36px}
</style>
</head>
<body>

<header class="site-header">
  <div class="abs lang-switch">
    <svg width="17" height="11" viewBox="0 0 17 11" aria-hidden="true"><rect width="17" height="11" fill="#1f3a7a"/><path d="M0 0L17 11M17 0L0 11" stroke="#fff" stroke-width="2"/><path d="M8.5 0V11M0 5.5H17" stroke="#fff" stroke-width="3"/><path d="M8.5 0V11M0 5.5H17" stroke="#c8102e" stroke-width="1.6"/></svg>
    Eng<span class="caret"></span>
  </div>
  <div class="abs brand-name">BRIGHT RETURNS</div>
  <a class="abs btn-dark">SHARE A STORY</a>
</header>

<nav class="abs main-nav">
  <ul>
    <li class="active">About Us</li>
    <li>Personal Sites</li>
    <li>Tips for Living</li>
    <li>News</li>
    <li>Resources</li>
    <li>Contact Us</li>
    <li>Search</li>
  </ul>
</nav>

<section class="abs hero">
  <h1>Sharing Stories and Giving Hope</h1>
  <p><span class="line">To people around the world who are facing inflammatory</span><span class="line">bowel disease, colorectal cancer, or have ostomy surgery</span></p>
  <a class="btn-outline" style="left:86px;width:162px">SHARE A STORY</a>
  <span class="or">or</span>
  <a class="btn-outline" style="left:326px;width:162px">READ STORIES</a>
  <div class="dots"><span></span><span></span><span></span><span></span></div>
  <div class="hero-photo" role="img" aria-label="Hiker in a red jacket standing on a rocky mountain peak under a cloudy blue sky"></div>
</section>

<main>
  <h2 class="col-title" style="left:86px">What is Bright Returns</h2>
  <div class="abs about-photo" role="img" aria-label="Climber in red standing on a snowy summit against a blue sky"></div>
  <p class="abs about-text"><span class="line">Our next wave of projects have been acqu</span><span class="line">ird during 2010 and 2011 and include a nu</span><span class="line">mbeof retail and residential developments.</span></p>

  <h2 class="col-title" style="left:449px">Share a Story</h2>
  <span class="abs qmark" style="left:454px;top:704px">“</span>
  <blockquote class="abs quote">
    <span class="line">Fusce feugiat malesuada odo. Morbi nuim</span>
    <span class="line">nc dogravida &nbsp;at, cursuis nc, lucitus a,loim</span>
    <span class="line">rem. Maecnas tristique ori acdim seim. Lo</span>
    <span class="line">rem ipsum dolorsit amet,cimonecteturiad</span>
    <span class="line">ipisicing elit, sed do eusmoimd tempor. Du</span>
    <span class="line">is autem vel eum iriure dolor hendrerit</span>
  </blockquote>
  <span class="abs qmark" style="left:724px;top:848px">”</span>
  <div class="abs avatar" role="img" aria-label="Portrait of the story author"></div>
  <div class="abs author-role">Maecenintty interu coquat</div>
  <div class="abs author-name">
    <svg width="16" height="16" viewBox="0 0 16 16" aria-hidden="true"><circle cx="8" cy="4.5" r="4" fill="#555"/><path d="M0 16c0-5 3.5-7 8-7s8 2 8 7z" fill="#555"/></svg>
    Dana Holt's
  </div>

  <h2 class="col-title" style="left:806px">News</h2>
  <article class="news-item" style="top:718px">
    <h3>TYPI NON HABENT CLARITATEM INSITAM;</h3>
    <time>26/11/2013</time>
    <p><span class="line">Typi non habent claritatem insitam; est len</span><span class="line">tis in iis qui facit eorum claritatem.</span></p>
  </article>
  <div class="abs news-rule"></div>
  <article class="news-item" style="top:873px">
    <h3>TYPI NON HABENT CLARITATEM INSITAM;</h3>
    <time>26/11/2013</time>
    <p><span class="line">Typi non habent claritatem insitam; est islen</span><span class="line">tis in iis qui facit eorum claritatem.</span></p>
  </article>
</main>

<footer class="abs site-footer">
  <div class="footer-links">Legal Notice | Privacy Policy | Site Map</div>
  <div class="copyright">Copyrights 2013. All Rights Reserved.</div>
  <span class="social" style="left:888px;background:var(--fb)" aria-label="Social link"></span>
  <span class="social" style="left:937px;background:var(--tw)" aria-label="Social link"></span>
  <span class="social" style="left:985px;background:var(--rss)" aria-label="Feed link"></span>
  <span class="social" style="left:1034px;background:var(--yt)" aria-label="Video link"></span>
</footer>

</body>
</html>
```